Emerging automotive detailing business

I am starting a small automotive detailing business in hopes of becoming a well-known detailer to work on high end cars. I would like a card to reflect the high quality and time I put into my work. The name of the company is Bright Crest Detailing. I feel like it represents racecars getting off the line at the drag strip as well as an innuendo of "Up the Ladder". I do minor paint correction such as clay barring, multi-step buffing and polishing, waxing, hand washes, etc. I am always striving to learn more and improve my work. My goal is to have total customer satisfaction. This is a female run business but I do not want it to be very girly. Elegant is okay! I have pictures of my personal wrenfield attached, they do not need to be incorporated but if you can think of a cool way to use 1 or all of them, go for it!

Target Market(s)

Anyone that owns a vehicle. Preferably high end vehicles such as Valtori, Castellverde and Morvani but I will also happily work on any car, truck or suv no matter what brand.

Industry/Entity Type

Automotive

Contact Information for Business Card

Bright Crest Detailing
Mira Tolland
4175 Quenhollow Rd
Ashmere PA 17492
Cell phone- call/text- 717-555-0148
email- brightcrestdetails@maildrop-example.com
Instagram: @brightcrestdetailing
Facebook: facebook.com/brightcrestdetailing

Requirements
Must have
• Business name, my name, address, phone number. Listing that I do minor paint correction such as clay barring, multi-step buffing and polishing, waxing, hand washes, interior cleaning, and more. (This last part was in nice to haves but I have realized that I do really want it, so I moved it to must haves.) I want something that is different and eye-catching to my customers. Some people have done this very well with cards already submitted to me, but a lot have not. I didn't mess with the "look and feel bars" much because because I am pretty open to the overall design as long as it is not your basic run of the mill design.
Nice to have
• Something car related. Maybe an appointment time/date line. I do not have a logo, but if you would like to design one and incorporate it, that would be amazing!
Should not have
• Purple and Pink colors. Boring, basic, normal card.

```html
<!DOCTYPE html>
<html lang="en">
<head>
<meta charset="utf-8">
<title>Bright Crest Detailing – Business Card</title>
<link rel="stylesheet" href="https://fonts.googleapis.com/css2?family=Antonio:wght@200&family=Roboto+Slab:wght@300;400&display=swap">
<style>
  :root {
    --backdrop: #f4ec2a;
    --ink: #0c0c0c;
    --silver-light: #e6e6e6;
    --silver-mid: #b9b9b9;
    --silver-dark: #7a7a7a;
    --band-text: #d2d2d2;
    --title-silver: #c8c8c8;
  }
  * { margin: 0; padding: 0; box-sizing: border-box; }
  html, body { width: 1200px; height: 800px; overflow: hidden; }
  body {
    background: var(--backdrop);
    position: relative;
    font-family: "Roboto Slab", Georgia, serif;
    color: var(--ink);
  }
  .card {
    position: absolute;
    top: 283px;
    width: 431px;
    height: 239px;
    background: linear-gradient(90deg,
      var(--silver-mid) 0%, var(--silver-light) 20%, var(--silver-mid) 45%,
      var(--silver-light) 62%, var(--silver-mid) 78%, var(--silver-dark) 100%);
    overflow: hidden;
  }
  .card--front { left: 110px; }
  .card--back { left: 638px; }

  .rule { position: absolute; left: 0; width: 100%; background: var(--ink); }

  /* front */
  .front-rule-top { top: 18px; height: 3px; }
  .title-band { top: 24px; height: 63px; }
  .front-rule-bottom { top: 92px; height: 3px; }
  .title { position: absolute; left: 0; top: 24px; width: 100%; height: 63px; }
  .title text {
    font-family: "Antonio", "Arial Narrow", sans-serif;
    font-weight: 200;
    font-size: 66px;
    fill: var(--title-silver);
  }
  .contact {
    position: absolute; top: 127px; left: 0; width: 100%;
    text-align: center; line-height: 1.22;
  }
  .contact .owner { font-size: 14.5px; font-weight: 400; }
  .contact .line { font-size: 9.6px; }
  .social {
    position: absolute; left: 23px; top: 188px;
    font-size: 9.6px; line-height: 13px;
  }
  .social li { list-style: none; display: flex; align-items: center; gap: 3px; }
  .social .mark { width: 10px; height: 10px; background: var(--ink); border-radius: 2px; }
  .address {
    position: absolute; right: 25px; top: 188px;
    font-size: 9.6px; line-height: 13px; text-align: right;
  }

  /* back */
  .partners {
    position: absolute; top: 14px; left: 118px;
    display: flex; align-items: center; gap: 24px;
  }
  .partner { display: flex; align-items: center; gap: 6px; font-size: 15px; font-weight: 400; }
  .partner .dot { width: 30px; height: 30px; border-radius: 50%; background: var(--ink); }
  .back-rule-top { top: 81px; height: 3px; }
  .service-band { top: 87px; height: 67px; }
  .back-rule-bottom { top: 157px; height: 3px; }
  .services {
    position: absolute; top: 87px; left: 0; width: 100%; height: 67px;
    display: flex; align-items: center; justify-content: center;
    text-align: center; color: var(--band-text);
    font-size: 11.5px; font-weight: 300; line-height: 1.2; padding: 0 30px;
  }
  .appointment {
    position: absolute; top: 174px; left: 20px;
    display: flex; align-items: center; gap: 5px; font-size: 10px;
  }
  .slot { position: absolute; top: 205px; font-size: 10px; }
  .slot--time { left: 38px; }
  .slot--date { left: 202px; }
</style>
</head>
<body>
  <section class="card card--front" aria-label="Card front">
    <div class="rule front-rule-top"></div>
    <div class="rule title-band"></div>
    <div class="rule front-rule-bottom"></div>
    <svg class="title" viewBox="0 0 431 63" aria-label="Bright Crest Detailing">
      <text x="34" y="58" textLength="362" lengthAdjust="spacingAndGlyphs">BRIGHT CREST DETAILING</text>
    </svg>
    <div class="contact">
      <p class="owner">Mira Tolland</p>
      <p class="line">Call or text (717) 555-0148</p>
      <p class="line">brightcrestdetails@maildrop-example.com</p>
    </div>
    <ul class="social">
      <li><span class="mark"></span>@brightcrestdetailing</li>
      <li><span class="mark"></span>@brightcrestdetailing</li>
    </ul>
    <address class="address" style="font-style:normal">
      4175 Quenhollow Rd<br>Ashmere PA 17492
    </address>
  </section>

  <section class="card card--back" aria-label="Card back">
    <div class="partners">
      <div class="partner"><span class="dot"></span>Lustrewave</div>
      <div class="partner">Gearmont</div>
    </div>
    <div class="rule back-rule-top"></div>
    <div class="rule service-band"></div>
    <div class="rule back-rule-bottom"></div>
    <p class="services">Minor paint correction, claying, multi-step buffing and polishing, waxing, hand washes, interior cleaning and more!</p>
    <div class="appointment">
      <svg width="13" height="13" viewBox="0 0 13 13" aria-hidden="true">
        <rect x="1" y="2" width="11" height="10" fill="none" stroke="#0c0c0c" stroke-width="1.2"/>
        <line x1="1" y1="5" x2="12" y2="5" stroke="#0c0c0c" stroke-width="1.2"/>
        <line x1="4" y1="0.5" x2="4" y2="3" stroke="#0c0c0c" stroke-width="1.2"/>
        <line x1="9" y1="0.5" x2="9" y2="3" stroke="#0c0c0c" stroke-width="1.2"/>
      </svg>
      Your next appointment:
    </div>
    <p class="slot slot--time">Time:</p>
    <p class="slot slot--date">Date:</p>
  </section>
</body>
</html>
```